Norrell Advisory WA Business Card

Create an interesting, eye catching and colourful two sided business card. We are a business consulting operation assisting SME's improve all areas of their business. We provide consulting services to assist SME's to create a culture of continuous improvement, making a positive difference in the business. Our tag line is Small changes, big rewards. We want to create a well recognised, innovative brand that can be continued throughout our website, social media and email correspondence.

Target Market(s)

Small to Medium Enterprise Business Owners

Industry/Entity Type

Business Consultant

Contact Information for Business Card

Name of Business: Norrell Advisory - Small Changes Big Rewards
Derek Holloway Ph 0407385510 Megan Holloway Ph 0407913847
Email norrelladvisorywa@mailbox-example.com
Web address TBA
FaceBook page TBA

BACKSIDE OF CARD

Providing assistance with:

• Organisation & Efficiency
• Revenue generation & Marketing
• Financial Management
• Production quality & delivery
• Systems & Process documentation
• Exit Strategy

Font styles to use
Other font styles liked:
• Calibri

Colors

Designer to choose colors to be used in the design.

Requirements
Must have
• Calibri font

```html
<!DOCTYPE html>
<html lang="en">
<head>
<meta charset="utf-8">
<title>Norrell Advisory WA – Business Card</title>
<link href="https://fonts.googleapis.com/css2?family=Carlito:wght@400;700&family=Cinzel:wght@400;500&family=Raleway:wght@400&display=swap" rel="stylesheet">
<style>
  :root {
    --backdrop: #2e2e2e;
    --card-white: #ffffff;
    --ink: #1e1e1e;
    --ink-soft: #444444;
    --brand-blue: #1f82c4;
    --accent-red: #e8372c;
    --rule: #555555;
    --grad-red: #ee4a3a;
    --grad-green: #8cc043;
    --grad-blue: #2b8fcb;
    --grad-yellow: #fbb936;
    --grad-violet: #7a64a0;
  }
  * { margin: 0; padding: 0; box-sizing: border-box; }
  html, body { width: 1200px; height: 1200px; overflow: hidden; }
  body {
    background: var(--backdrop);
    position: relative;
    font-family: "Carlito", "Calibri", sans-serif;
  }
  .card {
    position: absolute;
    top: 310px;
    width: 366px;
    height: 594px;
    text-align: center;
  }
  .card-front { left: 233px; background: var(--card-white); }
  .card-back {
    left: 628px;
    width: 368px;
    color: #fff;
    background:
      radial-gradient(ellipse 70% 45% at 100% 0%, var(--grad-green) 0%, rgba(140,192,67,0) 70%),
      radial-gradient(ellipse 70% 40% at 0% 100%, var(--grad-yellow) 0%, rgba(251,185,54,0) 70%),
      linear-gradient(155deg, var(--grad-red) 0%, var(--grad-red) 22%, var(--grad-violet) 40%, var(--grad-blue) 52%, var(--grad-violet) 64%, var(--grad-red) 78%, var(--grad-blue) 100%);
    background-color: var(--grad-red);
  }

  /* front */
  .brand-mark {
    position: absolute; left: 153px; top: 105px;
    width: 60px; height: 60px;
    background: var(--brand-blue);
  }
  .brand-name {
    position: absolute; left: 0; right: 0; top: 250px;
    font-family: "Cinzel", serif; font-weight: 500;
    font-size: 28px; line-height: 34px; color: var(--ink); letter-spacing: 0.3px;
    white-space: nowrap;
  }
  .tagline {
    position: absolute; left: 0; right: 0; top: 283px;
    font-family: "Raleway", sans-serif; font-size: 13.5px;
    letter-spacing: 2.6px; color: var(--ink-soft); white-space: nowrap;
  }
  .person { position: absolute; left: 0; right: 0; }
  .person-1 { top: 352px; }
  .person-2 { top: 418px; }
  .person-name {
    font-family: "Cinzel", serif; font-weight: 400;
    font-size: 26px; color: var(--brand-blue); line-height: 30px;
    white-space: nowrap;
  }
  .person-phone { font-size: 16px; color: var(--ink); line-height: 20px; }
  .person-phone .label { color: var(--accent-red); }
  .divider {
    position: absolute; left: 70px; width: 237px; top: 480px;
    border-top: 1.5px solid var(--rule);
  }
  .contacts {
    position: absolute; left: 0; right: 0; top: 490px;
    list-style: none; font-size: 17px; line-height: 21px; color: var(--ink);
  }

  /* back */
  .back-mark {
    position: absolute; left: 124px; top: 90px;
    width: 120px; height: 120px; background: #fff;
  }
  .back-name {
    position: absolute; left: 0; right: 0; top: 228px;
    font-family: "Cinzel", serif; font-weight: 500; font-size: 24px; color: #fff;
    white-space: nowrap;
  }
  .services-title {
    position: absolute; left: 0; right: 0; top: 348px;
    font-weight: 700; font-size: 23px; line-height: 28px; text-transform: uppercase;
    white-space: nowrap;
  }
  .services {
    position: absolute; left: 0; right: 0; top: 392px;
    list-style: none; font-size: 18px; font-weight: 700; line-height: 27px;
    text-transform: uppercase; white-space: nowrap;
  }
</style>
</head>
<body>
  <section class="card card-front" aria-label="Business card front">
    <div class="brand-mark" aria-hidden="true"></div>
    <h1 class="brand-name">NORRELL ADVISORY</h1>
    <p class="tagline">STEADY STEPS * LASTING GAINS</p>

    <div class="person person-1">
      <h2 class="person-name">DEREK HOLLOWAY</h2>
      <p class="person-phone"><span class="label">M:</span> 0407385510</p>
    </div>
    <div class="person person-2">
      <h2 class="person-name">MEGAN HOLLOWAY</h2>
      <p class="person-phone"><span class="label">M:</span> 0407913847</p>
    </div>

    <div class="divider"></div>
    <ul class="contacts">
      <li>norrelladvisorywa@mailbox-example.com</li>
      <li>www.norrelladvisory-example.com</li>
      <li>social.example/norrelladvisory</li>
    </ul>
  </section>

  <section class="card card-back" aria-label="Business card back">
    <div class="back-mark" aria-hidden="true"></div>
    <p class="back-name">NORRELL ADVISORY</p>
    <h2 class="services-title">Providing assistance with:</h2>
    <ul class="services">
      <li>Organisation &amp; Efficiency</li>
      <li>Revenue Generation &amp; Marketing</li>
      <li>Financial Management</li>
      <li>Production Quality &amp; Delivery</li>
      <li>Systems &amp; Process Documentation</li>
      <li>Exit Strategy</li>
    </ul>
  </section>
</body>
</html>
```